Modern, traditional Catering Menu for hotel and conference centre

Modernization of Catering menu while still making this very legible and clear to all guests. Template required in Microsoft word document so that updates to menu items can be easily updated. Menu needs style relatable to hotel and conference centre in an area known for apples, farming and awe-inspiring landscape.

Target Market(s)

Conference and meeting groups,

Industry/Entity Type

Hospitality

Font styles to use
Serif
Script

Colors

Designer to choose colors to be used in the design.

Requirements
Must have
• Legible and clear headers and modern look.
• Microsoft word template to easily be able to make updates.
Nice to have
• Something unique related to apples and our logo

```html
<!DOCTYPE html>
<html lang="en">
<head>
<meta charset="utf-8">
<title>Crabtree Ridge Inn – Catering Menu – Table of Content</title>
<link href="https://fonts.googleapis.com/css2?family=Crimson+Pro:wght@400;600&family=Kaushan+Script&display=swap" rel="stylesheet">
<style>
  :root {
    --backdrop: #e4e5e7;
    --paper: #ffffff;
    --ink: #2a1a14;
    --heading: #2b0f0c;
    --accent-red: #c0213a;
    --title-band: rgba(255, 226, 92, 0.82);
    --harvest-light: #f0c24a;
    --harvest-mid: #c98f2a;
    --harvest-deep: #6e3a14;
  }
  * { box-sizing: border-box; margin: 0; padding: 0; }
  html, body {
    width: 1200px;
    height: 1200px;
    overflow: hidden;
    background: var(--backdrop);
  }
  .menu-page {
    position: absolute;
    left: 126px;
    top: 0;
    width: 947px;
    height: 1200px;
    background: var(--paper);
    font-family: "Crimson Pro", Georgia, serif;
    color: var(--ink);
  }
  .hero-photo {
    position: absolute;
    left: 0;
    top: 0;
    width: 947px;
    height: 400px;
    background:
      radial-gradient(ellipse at 22% 30%, #b0262a 0 12%, transparent 24%),
      radial-gradient(ellipse at 70% 40%, var(--harvest-light) 0, transparent 55%),
      linear-gradient(160deg, var(--harvest-deep) 0%, var(--harvest-mid) 45%, var(--harvest-light) 75%, var(--harvest-mid) 100%);
  }
  .title-band {
    position: absolute;
    left: 59px;
    top: 306px;
    width: 543px;
    height: 126px;
    background: var(--title-band);
  }
  .page-title {
    position: absolute;
    left: 35px;
    top: 6px;
    font-family: "Kaushan Script", cursive;
    font-weight: 400;
    font-size: 72px;
    color: var(--heading);
    white-space: nowrap;
  }
  .intro {
    position: absolute;
    left: 61px;
    top: 454px;
    width: 826px;
    font-size: 14px;
    line-height: 1.3;
    text-align: justify;
  }
  .intro p + p { margin-top: 16px; }
  .intro strong { font-weight: 600; }
  .contents {
    position: absolute;
    left: 61px;
    top: 570px;
    width: 747px;
    list-style: none;
  }
  .contents li {
    display: flex;
    align-items: baseline;
    height: 31.7px;
    font-size: 22px;
    font-weight: 600;
    color: var(--heading);
  }
  .contents .entry { white-space: nowrap; }
  .contents .leader {
    flex: 1;
    margin: 0 4px 0 3px;
    border-bottom: 3px dotted var(--heading);
    transform: translateY(-4px);
    width: 680px;
    max-width: 680px;
  }
  .contents .page-no {
    width: 60px;
    padding-left: 18px;
    color: var(--accent-red);
  }
  .tagline {
    position: absolute;
    left: 0;
    width: 947px;
    top: 1112px;
    text-align: center;
    font-family: "Kaushan Script", cursive;
    font-size: 22px;
    color: var(--heading);
  }
</style>
</head>
<body>
  <main class="menu-page">
    <div class="hero-photo" role="img" aria-label="Photo of red apples in a woven wooden basket resting on golden straw"></div>
    <div class="title-band">
      <h1 class="page-title">Table of Content</h1>
    </div>

    <section class="intro">
      <p>Thank you for choosing the Crabtree Ridge Inn. Please allow us to answer any questions you may have to make this experience the absolute best for you and your guests.</p>
      <p><strong>Please note:</strong>&nbsp; Gluten friendly and vegetarian choices are available on our catering menu upon request. Please advise your Sales Team member if there are any allergies or special food requirements. We do our very best to accommodate all dietary needs.</p>
    </section>

    <ol class="contents">
      <li><span class="entry">Table of Contents</span><span class="leader"></span><span class="page-no">1</span></li>
      <li><span class="entry">Our Facility</span><span class="leader"></span><span class="page-no">2</span></li>
      <li><span class="entry">Meeting Refreshments &amp; Packages</span><span class="leader"></span><span class="page-no">3</span></li>
      <li><span class="entry">Breakfast Selections</span><span class="leader"></span><span class="page-no">4</span></li>
      <li><span class="entry">Plated Lunch Selections</span><span class="leader"></span><span class="page-no">5</span></li>
      <li><span class="entry">Buffet Lunch Selections</span><span class="leader"></span><span class="page-no">6</span></li>
      <li><span class="entry">Design Your Own Lunch Buffet</span><span class="leader"></span><span class="page-no">7</span></li>
      <li><span class="entry">Reception Selections: Cold &amp; Hot Hors d'Oeuvres</span><span class="leader"></span><span class="page-no">8</span></li>
      <li><span class="entry">Hot Hors d'Oeuvres, Seafood &amp; Late Night Catering</span><span class="leader"></span><span class="page-no">10</span></li>
      <li><span class="entry">Plated Dinner Selections</span><span class="leader"></span><span class="page-no">12</span></li>
      <li><span class="entry">Design Your Own Dinner Buffet: Salads &amp; Accompaniments</span><span class="leader"></span><span class="page-no">15</span></li>
      <li><span class="entry">Design Your Own Dinner Buffet: Entrées</span><span class="leader"></span><span class="page-no">16</span></li>
      <li><span class="entry">Design Your Own Dinner Buffet: Desserts</span><span class="leader"></span><span class="page-no">17</span></li>
      <li><span class="entry">Grand Dinner Selections</span><span class="leader"></span><span class="page-no">18</span></li>
      <li><span class="entry">Special Event Wine Selections</span><span class="leader"></span><span class="page-no">19</span></li>
      <li><span class="entry">Crabtree Ridge Inn Catering Information</span><span class="leader"></span><span class="page-no">20</span></li>
    </ol>

    <p class="tagline">Why settle for one apple? When you can have the whole orchard...</p>
  </main>
</body>
</html>
```